Fin-Tech Firm Captivating Business Card Design

We need a logo design as well to compliment this business card.

We are a new startup based in Singapore called 'Brevora Technologies'.

We develop an array of financial solutions ranging from payment convenience to forex trading and remittance.

Our initial product is Pim - an application which allows user to pre-order food items which would be ready for pickup upon arrival.

We would like to see designs being in black and silver or whatever that looks appealing and exudes a fun and professional feel.

We're not picky as long as it doesn't look like common business cards will do.

I do have a current logo which i do not really like. It will be attached for reference sake

Info:

Brevora Technologies Pte. Ltd.
Company Registration no. 201678213K

FILE TO BE IN .AI and .PSD

Target Market(s)

-F&B (Online-Ordering)
-Finance(P2P Lending and Forex)

Industry/Entity Type

Finance

Contact Information for Business Card

Name
Position
Contact
Email
Address: 47 Merrow Street, Calder House, #14-03 Singapore 068215

Adrian Teo
Founder, Managing Director
+65 98471360
adrian.t@brevoratech.com

Kai Loh
Founder, Executive Director
+65 96603847
kai.l@brevoratech.com

Logo Text

Brevora Technologies

Font styles to use
Sans Serif

Requirements
Must have
• Something that has word play about link brev
• Minimalistic but also something that catches The Eye
• Gold/silver on white/black might be nice
• Animal logo ; horse, eagle, bull or bear
Nice to have
• Just make it look fun and cute
• Just a suggestion to make the Y of brevora stand out
Should not have
• Any landmarks of singapore
• Exclude Pte. Ltd.

```html
<!DOCTYPE html>
<html lang="en">
<head>
<meta charset="utf-8">
<title>Brevora Technologies – Business Card</title>
<link rel="stylesheet" href="https://fonts.googleapis.com/css2?family=Source+Sans+3:ital,wght@0,400;0,600;0,700;1,700&display=swap">
<style>
  :root {
    --backdrop: #000000;
    --card: #333438;
    --gold: #f2a818;
    --white: #ffffff;
    --muted: #8f8f93;
    --divider: rgba(255,255,255,0.12);
  }
  * { margin: 0; padding: 0; box-sizing: border-box; }
  html, body {
    width: 1200px; height: 900px; overflow: hidden;
    background: var(--backdrop);
    font-family: "Source Sans 3", "Myriad Pro", sans-serif;
  }
  .stage { position: relative; width: 1200px; height: 900px; }
  .card {
    position: absolute; top: 271px;
    width: 457px; height: 281px;
    background: var(--card);
    border-radius: 14px;
  }
  .card--front { left: 137px; }
  .card--back { left: 626px; }

  .brand-name {
    position: absolute; left: 22px; top: 119px;
    width: 190px; text-align: center;
    font-size: 28px; font-weight: 400; letter-spacing: 1px; line-height: 34px;
    color: var(--gold);
  }

  .divider {
    position: absolute; left: 208px; top: 78px;
    width: 1px; height: 130px; background: var(--divider);
  }
  .contact { position: absolute; left: 227px; top: 64px; color: var(--white); }
  .contact__name { font-size: 17px; font-weight: 700; color: var(--gold); line-height: 20px; }
  .contact__role { font-size: 13px; line-height: 18px; }
  .contact__address { font-size: 13px; line-height: 18px; margin-top: 15px; }
  .contact__lines { list-style: none; margin-top: 16px; font-size: 13px; line-height: 19px; }
  .contact__lines li { display: flex; align-items: center; gap: 7px; }
  .contact__lines svg { width: 9px; height: 9px; fill: var(--gold); }

  .registration {
    position: absolute; left: 0; right: 0; top: 239px;
    text-align: center; font-size: 15px; font-style: italic; font-weight: 700;
    color: var(--gold);
  }
  .registration__number { color: var(--white); }

  .wordmark {
    position: absolute; left: 0; right: 0; top: 98px;
    text-align: center; font-size: 46px; font-weight: 400; letter-spacing: 2px;
    color: var(--gold); line-height: 56px;
  }
  .entity {
    position: absolute; left: 0; right: 0; top: 158px;
    display: flex; justify-content: center; align-items: center; gap: 6px;
    font-size: 15px; color: var(--muted);
  }
  .entity::before, .entity::after {
    content: ""; width: 30px; height: 1px; background: var(--muted);
  }
</style>
</head>
<body>
<main class="stage">
  <section class="card card--front" aria-label="Business card front">
    <p class="brand-name">Brevora</p>
    <div class="divider"></div>
    <div class="contact">
      <p class="contact__name">Adrian Teo</p>
      <p class="contact__role">Founder, Managing Director</p>
      <p class="contact__address">47 Merrow Street, Calder House,<br>#14-03 Singapore 068215</p>
      <ul class="contact__lines">
        <li><svg viewBox="0 0 10 10"><path d="M2 0.5 L3.6 2.8 L2.7 3.8 Q3.8 6.2 6.2 7.3 L7.2 6.4 L9.5 8 L8.4 9.5 Q1 8.5 0.5 1.6 Z"/></svg>+65 98471360</li>
        <li><svg viewBox="0 0 10 10"><path d="M0 2 H10 V8.5 H0 Z M0.6 2.4 L5 5.6 L9.4 2.4" stroke="#333438" stroke-width="0.8"/></svg>adrian.t@brevoratech.com</li>
      </ul>
    </div>
    <p class="registration">Company Registration no. <span class="registration__number">201678213K</span></p>
  </section>

  <section class="card card--back" aria-label="Business card back">
    <p class="wordmark">BREVORA</p>
    <p class="entity">Technologies</p>
  </section>
</main>
</body>
</html>
```